DOUBLE SIDED BROCHURE NEEDED TO PROMOTE DOCTOR

I need a double sided DL size (99mm x 210mm) brochure, promoting a doctor seeing patients in a new area.

I want something professional. I have included the relevant information. I would also like the Dr's picture somwhere in the brochure, with a professional background. I wish to print these tomorrow, so i will pick a winner within 14 hours of posting this ad.

I have included an example of a brochures design that I recently saw, and its definietly a good starting point.

Industry/Entity Type

Medical

```html
<!DOCTYPE html>
<html lang="en">
<head>
<meta charset="utf-8">
<title>Dr. Karim Haddad – Surgeon Brochure</title>
<link rel="stylesheet" href="https://fonts.googleapis.com/css2?family=Didact+Gothic&family=Oswald:wght@600&family=Lato:ital,wght@0,400;0,700;1,400&family=Playfair+Display:wght@700&display=swap">
<style>
:root{
  --ink-teal:#174a4c;
  --accent-teal:#1f7f86;
  --white:#ffffff;
  --paper:#eef0f0;
  --ink:#222;
  --divider:#c9c9c9;
  --box-edge:#2a5b60;
}
*{margin:0;padding:0;box-sizing:border-box}
html,body{width:1131px;height:1200px;overflow:hidden;background:#fff}
.canvas{position:relative;width:1131px;height:1200px;background:#fff}
.divider{position:absolute;left:565px;top:0;width:1px;height:1200px;background:var(--divider)}
.panel{position:absolute;top:18px;height:1164px;overflow:hidden}
.panel--front{left:18px;width:531px}
.panel--back{left:582px;width:532px}
.panel svg.backdrop{position:absolute;inset:0}
.abs{position:absolute}

/* front */
.portrait{left:154px;top:126px;width:377px;height:500px;background:linear-gradient(160deg,#8a8f96 0%,#3a3f4a 45%,#1e2330 100%);clip-path:polygon(30% 0,75% 0,82% 30%,100% 40%,100% 100%,0 100%,0 70%,18% 58%,28% 32%)}
.doctor-name{left:27px;top:14px;font-family:"Didact Gothic",sans-serif;font-size:51px;line-height:50px;color:var(--ink-teal)}
.brand{left:212px;top:24px;display:flex;align-items:center;gap:10px}
.brand-dot{width:46px;height:46px;border-radius:50%;background:var(--accent-teal)}
.brand-name{font-family:"Didact Gothic",sans-serif;font-size:20px;line-height:24px;color:var(--ink-teal)}
.specialty{left:27px;top:136px;font-family:"Didact Gothic",sans-serif;font-weight:400;font-size:49px;line-height:53px;color:var(--ink-teal)}
.greeting{left:12px;top:548px;font-family:"Oswald",sans-serif;font-weight:600;font-size:33px;line-height:40px;letter-spacing:1px;color:var(--white);font-style:italic;text-shadow:1px 2px 3px rgba(0,0,0,.4)}
.intro{left:38px;width:440px;font-family:"Didact Gothic",sans-serif;font-size:24px;line-height:35px;color:var(--white);text-shadow:1px 1px 2px rgba(0,0,0,.35)}
.intro--first{top:600px}
.intro--second{top:770px}
.contact-box{left:22px;top:958px;width:488px;height:188px;background:linear-gradient(#f6f7f7,var(--paper));border:3px solid var(--box-edge);box-shadow:4px 4px 6px rgba(0,0,0,.4)}
.contact-heading{left:32px;top:922px;z-index:2;font-family:"Lato",sans-serif;font-weight:700;font-size:30px;line-height:36px;color:var(--white);text-shadow:1px 2px 3px rgba(0,0,0,.5)}
.contact-list{left:32px;top:972px;z-index:2;font-family:"Didact Gothic",sans-serif;font-size:19px;line-height:24px;color:var(--ink)}
.contact-label{color:var(--accent-teal);display:flex;align-items:center;gap:4px}
.contact-label svg{width:15px;height:15px;fill:var(--ink)}
.badge{left:222px;top:982px;width:326px;height:120px;z-index:2}
.badge-title{left:288px;top:996px;width:216px;z-index:3;text-align:center;font-family:"Playfair Display",serif;font-weight:700;font-size:29px;color:#3a3a3a;transform:rotate(4deg)}
.badge-sub{left:300px;top:1040px;width:192px;z-index:3;text-align:center;font-family:"Lato",sans-serif;font-size:18px;line-height:19px;color:var(--white);transform:rotate(4deg)}

/* back */
.lead{left:31px;top:12px;width:470px;font-family:"Didact Gothic",sans-serif;font-size:33px;line-height:60px;color:var(--white)}
.including{left:30px;top:312px;font-family:"Lato",sans-serif;font-weight:400;font-size:66px;line-height:80px;color:var(--white);text-shadow:2px 2px 4px rgba(0,0,0,.3)}
.focus-list{left:26px;top:410px;width:460px;list-style:none;font-family:"Didact Gothic",sans-serif;font-size:29px;line-height:44px;color:var(--white)}
.focus-list .right{text-align:right}
.focus-note{padding-left:60px;font-family:"Lato",sans-serif;font-style:italic;font-size:27px;line-height:36px}
.focus-list .wrap{margin-top:8px;line-height:43px}
.focus-list .wrap span{display:block;padding-left:24px}
.general-heading{left:34px;top:752px;width:470px;font-family:"Lato",sans-serif;font-weight:400;font-size:46px;line-height:44px;color:var(--white);text-shadow:1px 2px 3px rgba(0,0,0,.3)}
.general-list{left:34px;top:884px;list-style:none;font-family:"Didact Gothic",sans-serif;font-size:32px;line-height:49px;color:var(--white)}
.bullet::before{content:"\2022";margin-right:12px}
</style>
</head>
<body>
<div class="canvas">
  <div class="divider"></div>

  <section class="panel panel--front">
    <svg class="backdrop" width="531" height="1164" viewBox="0 0 531 1164" aria-hidden="true">
      <defs>
        <linearGradient id="sky" x1="0" y1="0" x2="0" y2="1">
          <stop offset="0" stop-color="#9fd8f4"/>
          <stop offset="1" stop-color="#e8f6fc"/>
        </linearGradient>
      </defs>
      <rect width="531" height="1164" fill="url(#sky)"/>
    </svg>
    <div class="abs portrait" role="img" aria-label="Portrait photograph of the surgeon in a dark blazer"></div>
    <svg class="backdrop" width="531" height="1164" viewBox="0 0 531 1164" aria-hidden="true">
      <defs>
        <linearGradient id="teal" x1="0" y1="0" x2="0" y2="1">
          <stop offset="0" stop-color="#2f6e78"/>
          <stop offset="1" stop-color="#1c4e5a"/>
        </linearGradient>
        <linearGradient id="tealLow" x1="0" y1="0" x2="0" y2="1">
          <stop offset="0" stop-color="#1d5566"/>
          <stop offset="1" stop-color="#3e7c86"/>
        </linearGradient>
      </defs>
      <polygon points="0,412 380,598 531,612 531,1164 0,1164" fill="url(#teal)" opacity=".0"/>
      <polygon points="0,412 400,596 0,596" fill="#2f6e78"/>
      <polygon points="0,596 531,530 531,1164 0,1164" fill="url(#teal)"/>
      <polygon points="0,800 531,530 531,1164 0,1164" fill="url(#tealLow)" opacity=".85"/>
    </svg>

    <div class="abs doctor-name">Karim<br>Haddad</div>
    <div class="abs brand">
      <span class="brand-dot"></span>
      <span class="brand-name">St Anselm<br>Harbourview Hospital</span>
    </div>
    <h1 class="abs specialty">General,<br>Breast &amp;<br>Endocrine<br>Surgeon</h1>

    <div class="abs greeting">DEAR DOCTORS,</div>
    <p class="abs intro intro--first">We are pleased to<br>announce that Dr. Karim Haddad is now consulting in Bayview, seeing public and private patients.</p>
    <p class="abs intro intro--second">With patients having the option of surgery at Coastal Health Campus, Westbrook Hospital or St. Anselm Riverside.</p>

    <div class="abs contact-box"></div>
    <div class="abs contact-heading">CONTACT DETAILS</div>
    <div class="abs contact-list">
      <div class="contact-label"><svg viewBox="0 0 24 24"><path d="M12 2a7 7 0 0 0-7 7c0 5 7 13 7 13s7-8 7-13a7 7 0 0 0-7-7zm0 9.5A2.5 2.5 0 1 1 12 6.5a2.5 2.5 0 0 1 0 5z"/></svg>Bayview Clinic:</div>
      <div>48 Linden Crescent</div>
      <div>Bayview WA 6999</div>
      <div class="contact-label"><svg viewBox="0 0 24 24"><path d="M6.6 10.8a15 15 0 0 0 6.6 6.6l2.2-2.2c.3-.3.7-.4 1-.2 1.1.4 2.3.6 3.6.6.6 0 1 .4 1 1V20c0 .6-.4 1-1 1A17 17 0 0 1 3 4c0-.6.4-1 1-1h3.5c.6 0 1 .4 1 1 0 1.3.2 2.5.6 3.6.1.3 0 .7-.2 1z"/></svg>Phone:</div>
      <div>1300 555 014</div>
      <div class="contact-label"><svg viewBox="0 0 24 24"><path d="M6 3h9l3 3v5h2a1 1 0 0 1 1 1v8a1 1 0 0 1-1 1H4a1 1 0 0 1-1-1v-8a1 1 0 0 1 1-1h2zm2 2v6h8V7h-2V5zm-2 9v2h4v-2z"/></svg>Please send all referrals by fax to</div>
      <div>(08) 5550 1427</div>
    </div>

    <svg class="abs badge" viewBox="0 0 326 120" aria-hidden="true">
      <defs>
        <linearGradient id="bz" x1="0" y1="0" x2="0" y2="1">
          <stop offset="0" stop-color="#b87838"/>
          <stop offset="1" stop-color="#e0a868"/>
        </linearGradient>
      </defs>
      <polygon points="50,56 120,54 118,92" fill="#b7b6b2"/>
      <path d="M84,46 L270,72 L248,116 Q180,128 96,98 Z" fill="url(#bz)"/>
      <polygon points="62,16 300,36 296,68 58,48" fill="#dcdfdf" stroke="#9a9d9d" stroke-width="2"/>
      <polygon points="296,40 326,54 300,66" fill="#b7b6b2"/>
    </svg>
    <div class="abs badge-title">GUARANTEED</div>
    <div class="abs badge-sub">appointment within<br>* TWO WEEKS *</div>
  </section>

  <section class="panel panel--back">
    <svg class="backdrop" width="532" height="1164" viewBox="0 0 532 1164" aria-hidden="true">
      <defs>
        <linearGradient id="backBg" x1="0" y1="0" x2="0" y2="1">
          <stop offset="0" stop-color="#1f5a5e"/>
          <stop offset=".45" stop-color="#2e6472"/>
          <stop offset="1" stop-color="#4b7a8c"/>
        </linearGradient>
        <linearGradient id="swoosh" x1="0" y1="1" x2="1" y2="0">
          <stop offset="0" stop-color="#6fb2b2" stop-opacity=".2"/>
          <stop offset="1" stop-color="#a6dcd8" stop-opacity=".9"/>
        </linearGradient>
      </defs>
      <rect width="532" height="1164" fill="url(#backBg)"/>
      <path d="M0,540 C200,420 380,260 532,30 L532,70 C400,280 220,440 0,560 Z" fill="url(#swoosh)"/>
      <path d="M0,520 C220,400 400,230 532,110 L532,140 C380,280 200,430 0,540 Z" fill="#5aa0a4" opacity=".5"/>
      <path d="M0,560 C200,470 380,360 532,260 L532,600 L0,600 Z" fill="#2c5f70" opacity=".35"/>
      <path d="M0,680 C180,760 360,840 532,900 L532,940 C360,880 180,790 0,700 Z" fill="#b5d0d6" opacity=".55"/>
      <path d="M0,700 C180,790 360,880 532,940 L532,1164 L0,1164 Z" fill="#3b6a7e" opacity=".35"/>
    </svg>

    <p class="abs lead">Dr. Haddad is a highly trained<br>specialised surgeon, in all<br>areas of Endocrine, Breast<br>and General<br>Surgery.</p>
    <h2 class="abs including">Including:</h2>
    <ul class="abs focus-list">
      <li class="right bullet">Thyroid Surgery</li>
      <li class="right bullet">Parathyroid surgery</li>
      <li class="focus-note">(including minimally invasive<br>parathyroidectomy)</li>
      <li class="wrap bullet">Breast Cancer Benign breast<span>lesions.</span></li>
    </ul>

    <h2 class="abs general-heading">All areas of General<br>surgery, such as:</h2>
    <ul class="abs general-list">
      <li class="bullet">Gallbladder surgery</li>
      <li class="bullet">Hernia surgery</li>
      <li class="bullet">Haemorrhoids</li>
      <li class="bullet">Carpal Tunnel</li>
      <li class="bullet">Vasectomy etc etc...</li>
    </ul>
  </section>
</div>
</body>
</html>
```